Oil and Gas Exploration and Production company needs a business card design

We need a business card design using our logo and colors in the logo. We want a mainstream design.

```html
<!DOCTYPE html>
<html lang="en">
<head>
<meta charset="utf-8">
<title>Sierra Crude — Business Card</title>
<link rel="stylesheet" href="https://fonts.googleapis.com/css2?family=Mulish:wght@400;600;800&display=swap">
<style>
  :root {
    --backdrop: #cfd3d4;
    --paper: #fbfbf9;
    --ink: #262524;
    --gold: #d49a1f;
    --card-black: #282726;
  }
  html, body {
    margin: 0;
    width: 1200px;
    height: 900px;
    overflow: hidden;
    background: var(--backdrop);
    font-family: "Mulish", sans-serif;
  }
  .stage {
    width: 1200px;
    height: 900px;
    display: flex;
    align-items: center;
    justify-content: center;
    gap: 56px;
  }
  .card {
    position: relative;
    width: 525px;
    height: 300px;
    box-sizing: border-box;
    box-shadow: 0 14px 30px rgba(0,0,0,0.16);
  }
  .card-front {
    background: var(--paper);
    color: var(--ink);
  }
  .brand {
    position: absolute;
    left: 38px;
    top: 40px;
    display: flex;
    align-items: center;
    gap: 12px;
  }
  .brand-dot {
    width: 26px;
    height: 26px;
    border-radius: 50%;
    background: var(--ink);
  }
  .brand-name {
    font-weight: 800;
    font-size: 40px;
    letter-spacing: -0.5px;
    color: var(--ink);
    line-height: 1;
  }
  .divider {
    position: absolute;
    left: 38px;
    right: 38px;
    top: 138px;
    height: 1px;
    background: var(--gold);
  }
  .contact-list {
    position: absolute;
    left: 38px;
    top: 160px;
    margin: 0;
    padding: 0;
    list-style: none;
    font-size: 15px;
    line-height: 24px;
    color: var(--ink);
  }
  .contact-list li {
    display: flex;
    align-items: center;
    gap: 10px;
  }
  .contact-list svg {
    width: 13px;
    height: 13px;
    flex: none;
  }
  .holder {
    position: absolute;
    right: 38px;
    bottom: 58px;
    text-align: right;
  }
  .holder-name {
    font-size: 22px;
    font-weight: 600;
    color: var(--gold);
    margin: 0;
  }
  .holder-role {
    font-size: 14px;
    margin: 4px 0 0;
    color: var(--ink);
  }
  .bottom-rule {
    position: absolute;
    left: 38px;
    right: 38px;
    bottom: 34px;
    height: 1px;
    background: var(--gold);
  }
  .card-back {
    background: var(--card-black);
    display: flex;
    align-items: center;
    justify-content: center;
    gap: 14px;
  }
  .card-back .brand-dot { background: var(--gold); width: 30px; height: 30px; }
  .card-back .brand-name { color: #ffffff; font-size: 38px; }
</style>
</head>
<body>
<main class="stage">
  <section class="card card-front" aria-label="Business card front">
    <div class="brand">
      <span class="brand-dot"></span>
      <span class="brand-name">Sierra Crude</span>
    </div>
    <div class="divider"></div>
    <ul class="contact-list">
      <li>
        <svg viewBox="0 0 16 16" aria-hidden="true"><path fill="#d49a1f" d="M3.6 1.5l2.3 2.6-1.3 1.8c.9 2 2.5 3.6 4.5 4.5l1.8-1.3 2.6 2.3-1.3 2.2C7.2 13.3 2.7 8.8 1.4 2.8z"/></svg>
        (555) 014-2290
      </li>
      <li>
        <svg viewBox="0 0 16 16" aria-hidden="true"><rect x="1.5" y="3.5" width="13" height="9" fill="none" stroke="#d49a1f" stroke-width="1.4"/><path d="M1.5 3.5L8 9l6.5-5.5" fill="none" stroke="#d49a1f" stroke-width="1.4"/></svg>
        info@sierracrude.com
      </li>
      <li>
        <svg viewBox="0 0 16 16" aria-hidden="true"><circle cx="8" cy="8" r="6.3" fill="none" stroke="#d49a1f" stroke-width="1.4"/><path d="M1.7 8h12.6M8 1.7c-2.6 3.5-2.6 9.1 0 12.6M8 1.7c2.6 3.5 2.6 9.1 0 12.6" fill="none" stroke="#d49a1f" stroke-width="1.2"/></svg>
        www.sierracrude.com
      </li>
    </ul>
    <div class="holder">
      <p class="holder-name">Daniel Hart</p>
      <p class="holder-role">CEO</p>
    </div>
    <div class="bottom-rule"></div>
  </section>

  <section class="card card-back" aria-label="Business card back">
    <span class="brand-dot"></span>
    <span class="brand-name">Sierra Crude</span>
  </section>
</main>
</body>
</html>
```